High-end construction company needs a business card design

We need a modern looking business card that draws people in, is memorable and looks so good people will want to sick it on their fridges.
On the first side what is needed are:
Logo
My name - Tomasz Brelwik
Title - Managing Director
Website - www.varkelt.co.uk
Email - tomasz@varkelt.co.uk
Telephone - 020 5194 6281
Mobile - 07845139072
On the back side was is needed is a list of all the services we provide:
-Kitchen Renovations
-Bathroom Renovations
-House Renovations
-Garage Conversions
-Extensions
-Loft Conversions
-Conservatories
-Carpentry
-Tiling
-Electrical
-Plumbing & Heating
-Bricklaying
-Landscaping
-Decorating
-Plastering
We would like the colours to be the same shades as on the logo with grey or black for the words.
Target Market(s)
Anyone who needs building work done
Contact Information for Business Card
This business card is for a construction company which strives to deliver excellent service and quality.
The look and feel of the card should represent this.
Requirements
Must have
- On the first side what is needed are:
Logo
My name - Tomasz Brelwik
Title - Managing Director
Website - www.varkelt.co.uk
Email - tomasz@varkelt.co.uk
Telephone - 020 5194 6281
Mobile - 07845139072
Nice to have
- Cool looking features

```html
<!DOCTYPE html>
<html lang="en">
<head>
<meta charset="utf-8">
<title>Varkelt Construction Ltd – Business Card</title>
<link rel="stylesheet" href="https://fonts.googleapis.com/css2?family=Open+Sans:wght@400;600;700&display=swap">
<style>
  :root {
    --canvas: #d9d9d9;
    --card-green: #72bd45;
    --deep-green: #4b8b3c;
    --frame-green: #4f9a3c;
    --band-light: #f2f5ef;
    --ink: #1f1f1f;
    --ink-soft: #333333;
  }
  * { box-sizing: border-box; margin: 0; padding: 0; }
  html, body {
    width: 1200px; height: 1000px; overflow: hidden;
    background: var(--canvas);
    font-family: "Open Sans", Arial, sans-serif;
    color: var(--ink);
  }
  .sheet {
    width: 1200px; height: 1000px;
    display: flex; align-items: center; justify-content: center; gap: 56px;
  }
  .card {
    position: relative;
    width: 502px; height: 288px;
    background: var(--card-green);
    overflow: hidden;
  }
  .card--front { border: 2px solid var(--deep-green); }
  .card--back { border: 5px solid var(--frame-green); }

  .front-panel { position: absolute; inset: 0; }

  .brand {
    position: absolute; left: 36px; top: 132px; width: 170px;
    text-align: center; color: var(--ink); font-weight: 700;
    line-height: 1;
  }
  .brand__mark {
    display: inline-block; width: 14px; height: 14px;
    background: var(--ink); margin-right: 6px; vertical-align: 3px;
  }
  .brand__name { font-size: 31px; letter-spacing: 1px; }
  .brand__sub { display: block; font-size: 9.5px; letter-spacing: 1.2px; margin-top: 5px; }

  .name-band {
    position: absolute; left: 210px; right: 0; top: 60px; height: 52px;
    background: linear-gradient(90deg, rgba(114,189,69,0) 0%, #c9dcc0 22%, var(--band-light) 38%, #b8d3ac 62%, var(--deep-green) 100%);
  }
  .person {
    position: absolute; left: 270px; top: 72px;
  }
  .person__name { font-size: 17px; font-weight: 700; letter-spacing: 0.6px; line-height: 1.1; }
  .person__title { font-size: 10.5px; letter-spacing: 1px; color: var(--ink-soft); margin-top: 2px; }

  .contacts { position: absolute; left: 268px; top: 144px; list-style: none; }
  .contacts li {
    display: flex; align-items: center; gap: 9px;
    font-size: 14px; height: 22px; letter-spacing: 0.3px;
  }
  .contacts svg { width: 11px; height: 11px; flex: none; }

  .services-band {
    position: absolute; left: 0; right: 0; top: 35px; height: 26px;
    background: linear-gradient(90deg, var(--frame-green) 0%, #a9cc99 30%, var(--band-light) 50%, #a9cc99 70%, var(--frame-green) 100%);
    display: flex; align-items: center; justify-content: center;
    font-size: 15px; font-weight: 700; letter-spacing: 0.5px;
  }
  .services {
    position: absolute; top: 89px; list-style: none;
  }
  .services--left { left: 58px; }
  .services--right { left: 278px; }
  .services li {
    font-size: 14.4px; height: 19.3px; line-height: 19.3px; letter-spacing: 0.2px;
    display: flex; align-items: center;
  }
  .services li::before {
    content: ""; width: 8px; height: 8px; border-radius: 50%;
    background: var(--ink); margin-right: 7px; flex: none;
  }
</style>
</head>
<body>
<main class="sheet">

  <section class="card card--front" aria-label="Business card front">
    <svg class="front-panel" viewBox="0 0 498 284" preserveAspectRatio="none" aria-hidden="true">
      <path d="M0 0 H112 C200 40 238 100 236 150 C234 210 190 260 120 284 H0 Z" fill="var(--deep-green)"/>
    </svg>

    <div class="brand">
      <span class="brand__name"><span class="brand__mark"></span>VARKELT</span>
      <span class="brand__sub">CONSTRUCTION LTD</span>
    </div>

    <div class="name-band"></div>
    <div class="person">
      <p class="person__name">TOMASZ BRELWIK</p>
      <p class="person__title">MANAGING DIRECTOR</p>
    </div>

    <ul class="contacts">
      <li>
        <svg viewBox="0 0 12 12"><rect x="2.5" y="0.5" width="7" height="11" rx="1.2" fill="none" stroke="#1f1f1f" stroke-width="1.4"/><rect x="4.5" y="9" width="3" height="1" fill="#1f1f1f"/></svg>
        07845139072
      </li>
      <li>
        <svg viewBox="0 0 12 12"><path d="M2.6 0.8 L4.6 3.4 L3.5 4.6 C4.3 6.3 5.7 7.7 7.4 8.5 L8.6 7.4 L11.2 9.4 L9.8 11.2 C5 10.6 1.4 7 0.8 2.2 Z" fill="#1f1f1f"/></svg>
        020 5194 6281
      </li>
      <li>
        <svg viewBox="0 0 12 12"><rect x="0.5" y="2" width="11" height="8" fill="#1f1f1f"/><path d="M0.8 2.4 L6 6.6 L11.2 2.4" fill="none" stroke="#72bd45" stroke-width="1"/></svg>
        TOMASZ@VARKELT.CO.UK
      </li>
      <li>
        <svg viewBox="0 0 12 12"><circle cx="6" cy="6" r="5.3" fill="#1f1f1f"/><path d="M0.8 6 H11.2 M6 0.8 C3.8 3.5 3.8 8.5 6 11.2 M6 0.8 C8.2 3.5 8.2 8.5 6 11.2" fill="none" stroke="#72bd45" stroke-width="0.7"/></svg>
        WWW.VARKELT.CO.UK
      </li>
    </ul>
  </section>

  <section class="card card--back" aria-label="Business card back">
    <div class="services-band">SERVICES</div>
    <ul class="services services--left">
      <li>KITCHEN RENOVATIONS</li>
      <li>BATHROOM RENOVATIONS</li>
      <li>HOUSE RENOVATIONS</li>
      <li>GARAGE CONVERSIONS</li>
      <li>EXTENSIONS</li>
      <li>LOFT CONVERSIONS</li>
      <li>CONSERVATORIES</li>
      <li>CARPENTRY</li>
    </ul>
    <ul class="services services--right">
      <li>TILING</li>
      <li>ELECTRICAL</li>
      <li>PLUMBING &amp; HEATING</li>
      <li>BRICKLAYING</li>
      <li>LANDSCAPING</li>
      <li>DECORATING</li>
      <li>PLASTERING</li>
    </ul>
  </section>

</main>
</body>
</html>
```